Brand new letterhead, business card, email signature etc.

We are a financial company in London, UK. Our website is www.marlowvane.com. We're wanting a complete remodel of the company colours, letter head, business cards, email signatures, etc. Looking to keep the same font for the company name. I have upload a colour palette that we want to work with. We're looking for company letterhead for outgoing letters/ correspondence, letterhead for internal documentation, email signatures, e-letters. etc. Ultimately we will redesign the entire website also. It is important that our clients get a strong, secure, warm, trustworthy, solid feeling and first impression.
Updates

Designs look the same

Target Market(s)

Institutional investors, (ultra) high net worth individuals

Industry/Entity Type

Finance, Invesments banking.

Font styles to use
Other font styles liked:
• Current font is "Champagne & Limousines"

Requirements
Must have
• Must use the colours provided on the PDF uploaded to the portal. The purple = main colour. The red = accent colour.
Nice to have
• Nice to use same font as now for the company name "Corvane". Font is "Champagne & Limousines". Nice to have some reference to the old logo flower, but only subtle.
Should not have
• Do not use the colour red from our website. Use the colours provided on the colour palette PDF that I uploaded in the portal.

```html
<!DOCTYPE html>
<html lang="en">
<head>
<meta charset="utf-8">
<title>Corvane Letterhead</title>
<link rel="stylesheet" href="https://fonts.googleapis.com/css2?family=Josefin+Sans:wght@300&family=Open+Sans:wght@400;600;700&display=swap">
<style>
  :root {
    --backdrop: #dcd9d5;
    --paper: #f0f0ef;
    --ink: #4a4a4a;
    --ink-soft: #5a5a5a;
    --brand-purple: #5a2d6e;
    --brand-purple-soft: #7a4e8c;
    --accent-red: #b8394e;
    --rule: #cfcbc4;
    --flower-tint: #e6e2e8;
  }
  * { box-sizing: border-box; margin: 0; padding: 0; }
  html, body { width: 1200px; height: 1200px; overflow: hidden; }
  body {
    background: var(--backdrop);
    font-family: "Open Sans", Arial, sans-serif;
    color: var(--ink);
    position: relative;
  }
  .letterhead {
    position: absolute;
    left: 159px; top: 30px;
    width: 882px; height: 1140px;
    background: var(--paper);
    box-shadow: 0 4px 18px rgba(0,0,0,0.12);
    overflow: hidden;
  }
  .flower-decoration {
    position: absolute;
    left: 480px; top: 0;
    width: 402px; height: 362px;
    background: radial-gradient(ellipse at 55% 50%, var(--flower-tint) 0%, rgba(230,226,232,0.5) 45%, rgba(240,240,239,0) 75%);
  }
  .brand {
    position: absolute;
    left: 126px; top: 86px;
    display: flex; align-items: center; gap: 12px;
  }
  .brand-mark {
    width: 50px; height: 50px;
    border: 1px solid var(--brand-purple);
  }
  .brand-name {
    font-family: "Josefin Sans", "Open Sans", sans-serif;
    font-weight: 300;
    font-size: 30px;
    letter-spacing: 0.2em;
    color: var(--brand-purple);
    text-transform: uppercase;
    padding-top: 6px;
  }
  .rule {
    position: absolute;
    height: 2px;
    background: var(--rule);
  }
  .rule::before {
    content: "";
    position: absolute; left: 0; top: -0.5px;
    height: 3px;
    background: var(--brand-purple);
  }
  .rule--head { left: 126px; top: 145px; width: 625px; }
  .rule--head::before { width: 51px; }
  .rule--foot { left: 125px; top: 1020px; width: 626px; }
  .rule--foot::before { width: 59px; }

  .sender { position: absolute; left: 126px; top: 236px; }
  .sender-name { color: var(--brand-purple); font-size: 14.5px; font-weight: 600; line-height: 20px; }
  .sender-title { font-size: 11px; line-height: 18px; color: var(--ink-soft); }
  .sender-line { font-size: 12.5px; line-height: 20px; white-space: nowrap; }
  .sender-line b { color: var(--accent-red); font-weight: 600; display: inline-block; width: 27px; }
  .sender-line b.dark { color: var(--ink); }

  .letter-date {
    position: absolute; right: 131px; top: 294px;
    font-size: 12.5px; line-height: 20px;
  }
  .letter-body {
    position: absolute; left: 126px; top: 352px;
    font-size: 12.5px; line-height: 26.6px; color: var(--ink);
  }
  .letter-body p { white-space: nowrap; margin-bottom: 26.6px; }

  .signature-stroke {
    position: absolute; left: 123px; top: 828px;
    width: 135px; height: 34px;
    background: linear-gradient(90deg, #d9d5dc, #e4e1e6);
    border-radius: 4px;
  }
  .signatory { position: absolute; left: 125px; top: 868px; line-height: 15px; }
  .signatory-name { font-size: 13px; font-weight: 700; color: #3a3a3a; }
  .signatory-role { font-size: 13px; color: var(--ink-soft); }

  .footer-contacts { position: absolute; top: 1050px; left: 0; width: 100%; }
  .contact { position: absolute; display: flex; align-items: center; gap: 14px; }
  .contact svg { flex: none; }
  .contact-text { font-size: 12.5px; line-height: 15px; color: var(--ink); white-space: nowrap; }
  .contact--phone { left: 137px; }
  .contact--mail { left: 336px; }
  .contact--place { left: 563px; }

  .footer-band {
    position: absolute; left: 0; bottom: 0;
    width: 100%; height: 23px;
    background: var(--brand-purple);
  }
</style>
</head>
<body>
  <main class="letterhead">
    <div class="flower-decoration" role="img" aria-label="Faint outline of a large flower as background decoration"></div>

    <header class="brand">
      <div class="brand-mark"></div>
      <div class="brand-name">Corvane</div>
    </header>
    <div class="rule rule--head"></div>

    <section class="sender">
      <div class="sender-name">Elias Hartwell</div>
      <div class="sender-title">Chief Director</div>
      <div class="sender-line"><b>A :</b>12 Fenwick Lane London - 4410</div>
      <div class="sender-line"><b class="dark">W :</b>office@corvane-mail.com, www.marlowvane.com</div>
      <div class="sender-line"><b>P :</b>+44 - 20715 - 3382</div>
    </section>
    <div class="letter-date">Date, 10 September, 2024</div>

    <article class="letter-body">
      <p>This is a sample letter that has been placed to demonstrate typing remat (Your Company). letterhead<br>design. When positioned properly, it will serve to work in harmony with all other elements letterhead.<br>This letterhead design is meant to project an image</p>
      <p>This letterhead design is meant project an image of professionalism reliability. By using simple aligen<br>we have created a very spacious feeling. The simplicity suggest&nbsp; rengththe spaciousnes contributes h<br>aesthetics the layout. These basic qualities along with the (Your Company)</p>
      <p>look and helps reinforce the (Your Company) brand. letterhead design is meant to project an image p<br>design. When positioned properly, it will serve to work in harmony all the other elements letterhead.<br>sionalism and reliability.</p>
      <p>This letterhead design is based on the (Form of your logo) form (Your Company) logo. Each stationery<br>we have created a very spacious feeling. The simplicity suggests strength the spaciousnes contribute<br>part of the (Form of your logo).</p>
    </article>

    <div class="signature-stroke" role="img" aria-label="Handwritten signature"></div>
    <div class="signatory">
      <div class="signatory-name">Elias Hartwell</div>
      <div class="signatory-role">Manager</div>
    </div>

    <div class="rule rule--foot"></div>
    <footer class="footer-contacts">
      <div class="contact contact--phone">
        <svg width="25" height="35" viewBox="0 0 25 35" aria-hidden="true">
          <rect x="1.5" y="1.5" width="22" height="32" rx="3" fill="none" stroke="#5a2d6e" stroke-width="2"/>
          <line x1="1.5" y1="6" x2="23.5" y2="6" stroke="#5a2d6e" stroke-width="1.5"/>
          <line x1="1.5" y1="28" x2="23.5" y2="28" stroke="#5a2d6e" stroke-width="1.5"/>
          <line x1="10" y1="31" x2="15" y2="31" stroke="#5a2d6e" stroke-width="1.2"/>
        </svg>
        <div class="contact-text">+44 207 153 3382<br>+44 207 153 3383</div>
      </div>
      <div class="contact contact--mail">
        <svg width="31" height="22" viewBox="0 0 31 22" aria-hidden="true">
          <rect x="1.5" y="1.5" width="28" height="19" rx="2" fill="none" stroke="#5a2d6e" stroke-width="2"/>
          <polyline points="2,3 15.5,13 29,3" fill="none" stroke="#5a2d6e" stroke-width="1.8"/>
          <line x1="2" y1="20" x2="12" y2="11" stroke="#5a2d6e" stroke-width="1.5"/>
          <line x1="29" y1="20" x2="19" y2="11" stroke="#5a2d6e" stroke-width="1.5"/>
        </svg>
        <div class="contact-text">info@marlowvane.com<br>hartwell@marlowvane.com</div>
      </div>
      <div class="contact contact--place">
        <svg width="27" height="35" viewBox="0 0 27 35" aria-hidden="true">
          <path d="M13.5 33 C7 24 2 18 2 12.5 A11.5 11.5 0 0 1 25 12.5 C25 18 20 24 13.5 33 Z" fill="none" stroke="#5a2d6e" stroke-width="2"/>
          <circle cx="13.5" cy="12.5" r="5" fill="none" stroke="#5a2d6e" stroke-width="1.8"/>
        </svg>
        <div class="contact-text">18 Ashgrove Street<br>London, EC2V 7HN</div>
      </div>
    </footer>
    <div class="footer-band"></div>
  </main>
</body>
</html>
```